Lanternfield Drinks business cards

We need a business card design for our new logo. The company is modern, progressive, professional, yet approachable. The key products are ready to drink bottles and cans of coffee based beverages.
These cards will be a critical part of the first impression made by our sales organization, business development team, and all external facing personnel.
Card can be a vertical or horizontal orientation.

Target Market(s)

Customers, suppliers, business partners

Industry/Entity Type

Business

Contact Information for Business Card

Business cards should feature Company Name and Logo.

Font styles to use
Serif

Colors

Designer to choose colors to be used in the design.

Requirements
Must have
• Strong readability of Name, phone #, mobile number and email address.
• Job title, website url, Street Address, and other details can be secondary level readability.
Nice to have
• High impact, simplistic quality design.
• Ok to utilize the 'H in the box' separate from the company name

```html
<!DOCTYPE html>
<html lang="en">
<head>
<meta charset="utf-8">
<title>Lanternfield Drinks Business Cards</title>
<link rel="stylesheet" href="https://fonts.googleapis.com/css2?family=Cinzel:wght@500;700&family=Open+Sans:wght@400&display=swap">
<style>
  :root {
    --backdrop: #8e8d8b;
    --card-light: #ececec;
    --card-dark: #000000;
    --accent: #ee5a2b;
    --rule: #f0b89f;
    --ink: #3a3a3a;
    --white: #ffffff;
  }
  * { box-sizing: border-box; margin: 0; padding: 0; }
  html, body { width: 1200px; height: 900px; overflow: hidden; }
  body { background: var(--backdrop); position: relative; font-family: "Open Sans", sans-serif; }

  .card { position: absolute; top: 170px; width: 347px; height: 560px; box-shadow: 3px 4px 6px rgba(0,0,0,.35); }
  .card--front { left: 259px; background: var(--card-light); }
  .card--back { left: 631px; background: var(--card-dark); }

  .brand-mark { position: absolute; left: 132px; top: 90px; width: 84px; height: 84px; border: 3px solid var(--accent); }
  .brand-name {
    position: absolute; left: 0; width: 100%; text-align: center;
    font-family: "Cinzel", serif; font-weight: 700; line-height: 1.05;
  }
  .card--front .brand-name { top: 188px; font-size: 33px; color: var(--accent); }
  .card--back .brand-name { top: 248px; font-size: 34px; color: var(--white); }

  .holder { position: absolute; top: 318px; width: 100%; text-align: center; }
  .holder__name { font-family: "Cinzel", serif; font-weight: 500; font-size: 21px; color: var(--accent); letter-spacing: .3px; }
  .holder__title { font-size: 14px; color: var(--ink); margin-top: 2px; }

  .divider { position: absolute; left: 92px; width: 164px; display: flex; align-items: center; justify-content: center; gap: 5px; }
  .divider::before, .divider::after { content: ""; flex: 1; height: 1px; background: var(--rule); }
  .divider--contact { top: 377px; }
  .divider--address { top: 465px; }
  .icon { width: 16px; height: 16px; background: var(--accent); display: flex; align-items: center; justify-content: center; }
  .icon svg { width: 11px; height: 11px; }

  .details { position: absolute; width: 100%; text-align: center; font-size: 14.5px; color: var(--ink); line-height: 20px; }
  .details--contact { top: 400px; }
  .details--address { top: 486px; }

  .website { position: absolute; bottom: 38px; width: 100%; text-align: center; color: var(--white); font-size: 16px; letter-spacing: 1.5px; }
</style>
</head>
<body>
  <section class="card card--front">
    <div class="brand-mark"></div>
    <h1 class="brand-name">LANTERNFIELD<br>DRINKS</h1>
    <div class="holder">
      <p class="holder__name">Daniel Marsh</p>
      <p class="holder__title">Managing Director</p>
    </div>
    <div class="divider divider--contact">
      <span class="icon"><svg viewBox="0 0 12 12"><path fill="#fff" d="M1 4c0-1.5 2.5-2.5 5-2.5S11 2.5 11 4l-2 1-1-1.5H4L3 5zM3 6h6l1 4.5H2z"/></svg></span>
      <span class="icon"><svg viewBox="0 0 12 12"><rect x="3" y="0.5" width="6" height="11" rx="1" fill="#fff"/><rect x="4" y="2" width="4" height="7" fill="#ee5a2b"/></svg></span>
      <span class="icon"><svg viewBox="0 0 12 12"><rect x="1" y="2.5" width="10" height="7" fill="#fff"/><path d="M1 2.5l5 4 5-4" fill="none" stroke="#ee5a2b" stroke-width="1"/></svg></span>
    </div>
    <div class="details details--contact">
      <p>044-123 456 789</p>
      <p>044-123 456 789</p>
      <p>info@webname.com</p>
    </div>
    <div class="divider divider--address">
      <span class="icon"><svg viewBox="0 0 12 12"><path fill="#fff" d="M6 11.5L2.5 6A3.5 3.5 0 1 1 9.5 6z"/><circle cx="6" cy="4.5" r="1.3" fill="#ee5a2b"/></svg></span>
    </div>
    <div class="details details--address">
      <p>12345, Address Goes Here</p>
      <p>Country Name, 123456.</p>
    </div>
  </section>

  <section class="card card--back">
    <h2 class="brand-name">LANTERNFIELD<br>DRINKS</h2>
    <p class="website">WWW.WEBNAME.COM</p>
  </section>
</body>
</html>
```